Brightvale cleaning and maintenance company

An expansive website whereby we can advertise our commercial cleaning and maintenance services across a service portfolio of commercial cleaning and property maintenance. Whereby potential skilled resources can deposit there resume so we can collaborate and match candidates to a broad range of cleaning and maintenance jobs/projects.
Updates

Looking for more extensive ideas so the front page can change pictures on it with the focus for Brightvale Commercial Cleaning and Maintenance. Also need to bring in all the portfolios we offer including 1. Equipment Cleaning and Sanitisation Services 2. High pressure gurney and play ground equipment cleaning 3. General Cleaning and Property Facilities Management 4. Project and Recruiting Services, to allow for potential professional cleaners, handy man, mechanics, warehousing resources , electricians to deposit there resume. Most of the designers have stuck with the old portfolio categories , however the portfolio of services we offer has been updated so that needs to be reflected in the website. Also not necessary to use all my original photos I would like the opening page of the website to perhaps be able to change and have different pictures is that possible thank you

```html
<!DOCTYPE html>
<html lang="en">
<head>
<meta charset="utf-8">
<title>Brightvale — Commercial Cleaning and Maintenance</title>
<link rel="stylesheet" href="https://fonts.googleapis.com/css2?family=Montserrat:wght@600;700;800&family=Roboto:wght@400;500;700&display=swap">
<style>
:root{
  --navy:#12377a;
  --navy-deep:#0c2a63;
  --orange:#fb3c07;
  --ink:#1d2433;
  --muted:#6b7280;
  --gray:#f1f1f1;
  --white:#ffffff;
}
*{box-sizing:border-box;margin:0;padding:0}
html,body{width:1200px;height:5029px;overflow:hidden}
body{font-family:"Roboto",Arial,sans-serif;color:var(--ink);background:var(--white);position:relative}
a{color:inherit;text-decoration:none}
.abs{position:absolute}
h1,h2,h3,.heading{font-family:"Montserrat",Arial,sans-serif}
.accent{color:var(--orange)}
.btn{display:inline-flex;align-items:center;gap:8px;background:var(--orange);color:#fff;font-weight:700;border-radius:30px;font-size:14px;justify-content:center}
.btn .dot{width:13px;height:13px;border-radius:50%;background:#fff;display:inline-block;position:relative}
.btn .dot::after{content:"";position:absolute;left:4px;top:3.5px;border-left:5px solid var(--orange);border-top:3px solid transparent;border-bottom:3px solid transparent}

/* header */
.site-header{position:absolute;left:0;top:0;width:1200px;height:101px;background:#fff}
.brand{position:absolute;left:111px;top:32px;display:flex;align-items:center;gap:10px;font-family:"Montserrat",sans-serif;font-weight:700;font-size:28px;color:var(--navy)}
.brand-mark{width:36px;height:36px;border-radius:50%;background:var(--navy)}
.main-nav{position:absolute;left:441px;top:42px;display:flex;gap:21px;font-size:14px;font-weight:500}
.header-call{position:absolute;left:911px;top:29px;width:177px;height:46px;font-size:14px}

/* hero */
.hero{position:absolute;left:0;top:101px;width:1200px;height:640px;overflow:hidden}
.hero-photo{position:absolute;inset:0;background:linear-gradient(100deg,#8c9aa3 0%,#c2c7c4 30%,#6f7d56 55%,#a45a3a 80%,#8d9a6e 100%)}
.hero-copy{position:absolute;right:113px;top:165px;text-align:right;color:#fff}
.hero-copy h1{font-size:42px;font-weight:700;letter-spacing:1px}
.hero-copy p{font-size:17px;font-weight:700;line-height:23px;margin-top:6px}
.hero-copy .btn{margin-top:16px;width:205px;height:47px;font-size:16px}
.arrow-btn{position:absolute;top:268px;width:40px;height:40px;border:2px solid #fff;border-radius:50%}
.arrow-btn svg{position:absolute;left:11px;top:11px}
.hero-curve{position:absolute;left:0;bottom:0}

/* references */
.references{position:absolute;left:0;top:741px;width:1200px;height:114px;background:var(--gray)}
.references p{position:absolute;left:111px;top:33px;font-family:"Montserrat",sans-serif;font-weight:700;font-size:16px;color:var(--navy)}
.ref-badge{position:absolute;top:13px;width:176px;height:67px;background:#fff;border:1px solid #e1e1e1;display:flex;align-items:center;justify-content:center}
.ref-badge span{width:70px;height:40px;border-radius:6px;background:#d7d9de}

/* working */
.working{position:absolute;left:0;top:855px;width:1200px;height:651px;background:#fff}
.section-title{text-align:center;font-size:34px;font-weight:800;color:var(--navy);letter-spacing:.5px}
.working .section-title{position:absolute;left:0;width:1200px;top:102px}
.working .lead{position:absolute;left:0;width:1200px;top:153px;text-align:center;font-size:15px;color:#555}
.value-card{position:absolute;top:224px;width:299px;height:306px;background:#fff;border-radius:10px;box-shadow:0 4px 18px rgba(0,0,0,.1);text-align:center}
.value-card.active{border-bottom:5px solid var(--orange);height:311px}
.value-icon{width:88px;height:88px;border-radius:50%;margin:16px auto 0;background:var(--navy);display:flex;align-items:center;justify-content:center}
.value-icon.orange{background:var(--orange)}
.value-card h3{font-family:"Roboto",sans-serif;font-weight:500;font-size:18px;margin-top:21px}
.value-card p{font-size:14px;line-height:24px;color:#555;margin:12px 26px 0}
.value-card .more{display:block;margin-top:13px;font-size:14px;font-weight:700;color:var(--orange)}

/* services */
.services{position:absolute;left:0;top:1506px;width:1200px;height:927px;background:var(--navy)}
.services .eyebrow{position:absolute;left:0;width:1200px;top:72px;text-align:center;color:#fff;font-size:14px;font-weight:500}
.services .section-title{position:absolute;left:0;width:1200px;top:96px;color:#fff}
.service-card{position:absolute;width:472px;height:258px;overflow:hidden}
.service-photo{position:absolute;inset:0}
.service-text{position:absolute;left:14px;top:26px;width:210px;color:#fff}
.service-text h3{font-family:"Roboto",sans-serif;font-size:17px;font-weight:700;line-height:25px}
.service-text p{font-size:14px;line-height:25px;margin-top:10px;color:#e6e9f1}
.service-text .more{display:block;margin-top:12px;font-size:14px;font-weight:700;color:var(--orange)}
.services .btn{position:absolute;left:467px;top:803px;width:266px;height:50px}

/* company */
.company{position:absolute;left:0;top:2433px;width:1200px;height:572px;background:#fff}
.company-photo{position:absolute;left:117px;top:84px;width:420px;height:420px;border-radius:50%;background:radial-gradient(circle at 50% 50%,#8c9bb0 0%,#4d5d78 60%,#2f3d55 100%)}
.company h2{position:absolute;left:601px;top:117px;font-size:34px;font-weight:800;color:var(--navy)}
.company p{position:absolute;left:599px;top:180px;width:488px;font-size:15px;line-height:29px;color:#555}
.company .btn{position:absolute;left:599px;top:421px;width:165px;height:47px}

/* portfolio */
.portfolio{position:absolute;left:0;top:3005px;width:1200px;height:936px;background:var(--gray)}
.portfolio .section-title{position:absolute;left:0;width:1200px;top:118px}
.tile{position:absolute}
.portfolio .btn{position:absolute;left:518px;top:763px;width:164px;height:47px}

/* contact */
.contact{position:absolute;left:0;top:3941px;width:1200px;height:624px;background:#fff}
.touch-box{position:absolute;left:111px;top:98px;width:398px;height:429px;background:var(--orange);color:#fff;padding:34px 0 0 37px}
.touch-box h2{font-size:26px;font-weight:700}
.touch-item{position:relative;padding-left:52px;margin-top:30px}
.touch-item .ico{position:absolute;left:0;top:2px;width:34px;height:34px;border-radius:50%;background:#fff;display:flex;align-items:center;justify-content:center}
.touch-item h3{font-size:18px;font-weight:700}
.touch-item p{font-size:13.5px;line-height:17px;margin-top:2px}
.contact-form{position:absolute;left:568px;top:106px;width:445px}
.contact-form h2{font-size:28px;font-weight:700;color:var(--ink)}
.field{position:absolute;border-bottom:1px solid #cfd3da;height:30px;font-size:12px;color:#777;display:flex;align-items:center;gap:6px}
.contact-form .btn{position:absolute;left:0;top:366px;width:147px;height:38px}

/* footer */
.site-footer{position:absolute;left:0;top:4565px;width:1200px;height:464px;background:var(--navy-deep);color:#fff}
.footer-col{position:absolute;top:151px}
.footer-col h4{font-family:"Roboto",sans-serif;font-size:15px;font-weight:500;margin-bottom:20px}
.footer-col li{list-style:none;font-size:13px;line-height:27px}
.info-row{display:flex;gap:12px;font-size:13px;line-height:16px;margin-bottom:12px;align-items:flex-start}
.social{display:flex;align-items:center;gap:12px;font-size:13px;margin-bottom:11px}
.social span{width:24px;height:24px;border-radius:50%;background:var(--orange)}
.copyright{position:absolute;left:0;width:1200px;top:372px;text-align:center;font-size:13px}
</style>
</head>
<body>

<header class="site-header">
  <a class="brand" href="#"><span class="brand-mark"></span>Brightvale</a>
  <nav class="main-nav">
    <a href="#">Home</a><a href="#">Services</a><a href="#">About Us</a><a href="#">Safety &amp; Compliance</a><a href="#">Contact</a>
  </nav>
  <a class="btn header-call" href="#">
    <svg width="13" height="13" viewBox="0 0 24 24"><path fill="#fff" d="M6.6 10.8a15.2 15.2 0 006.6 6.6l2.2-2.2a1 1 0 011-.25 11.4 11.4 0 003.6.6 1 1 0 011 1V20a1 1 0 01-1 1A17 17 0 013 4a1 1 0 011-1h3.5a1 1 0 011 1c0 1.25.2 2.45.6 3.6a1 1 0 01-.25 1z"/></svg>
    (07) 5510 204
  </a>
</header>

<section class="hero">
  <div class="hero-photo" role="img" aria-label="Cleaner in blue overalls using a high pressure hose on a garden path"></div>
  <div class="arrow-btn" style="left:34px"><svg width="14" height="14" viewBox="0 0 14 14"><path d="M9 2L4 7l5 5" fill="none" stroke="#fff" stroke-width="2"/></svg></div>
  <div class="arrow-btn" style="left:1130px"><svg width="14" height="14" viewBox="0 0 14 14"><path d="M5 2l5 5-5 5" fill="none" stroke="#fff" stroke-width="2"/></svg></div>
  <div class="hero-copy">
    <h1>BRIGHTVALE</h1>
    <p>Your source for commercial and food service<br>equipment cleaning.</p>
    <a class="btn" href="#">GET STARTED <span class="dot"></span></a>
  </div>
  <svg class="hero-curve" width="1200" height="120" viewBox="0 0 1200 120">
    <path d="M0 70 Q600 150 1200 70 V120 H0Z" fill="#f1f1f1"/>
    <path d="M90 52 Q600 130 1110 52 Q600 100 90 52Z" fill="#fb3c07"/>
    <circle cx="600" cy="55" r="31" fill="#fff"/>
    <circle cx="600" cy="55" r="15" fill="#12377a"/>
  </svg>
</section>

<section class="references">
  <p>References Business <span class="accent">Relationship</span></p>
  <div class="ref-badge" style="left:455px"><span></span></div>
  <div class="ref-badge" style="left:683px"><span></span></div>
  <div class="ref-badge" style="left:912px"><span></span></div>
</section>

<section class="working">
  <h2 class="section-title">WORKING WITH <span class="accent">BRIGHTVALE</span></h2>
  <p class="lead">We are Brightvale, a leading, Australian owned, cleaning services company.</p>

  <article class="value-card" style="left:111px">
    <div class="value-icon"><svg width="50" height="50" viewBox="0 0 50 50" fill="none" stroke="#fff" stroke-width="2.5"><circle cx="25" cy="25" r="20"/><circle cx="25" cy="25" r="12"/><circle cx="25" cy="25" r="4" fill="#fff"/></svg></div>
    <h3>OUR PURPOSE</h3>
    <p>To support and extend the life of equipment, maximize product yield and achieve high quality hygiene standards for our food and equipment service</p>
    <a class="more" href="#">LEARN MORE &nbsp;»</a>
  </article>
  <article class="value-card active" style="left:451px">
    <div class="value-icon orange"><svg width="50" height="50" viewBox="0 0 50 50" fill="none" stroke="#fff" stroke-width="2.5"><rect x="9" y="12" width="32" height="24" rx="2"/><path d="M16 30v-6M23 30v-10M30 30v-8M37 30v-13"/></svg></div>
    <h3>OUR VISION</h3>
    <p>A sustainable food service and equipment cleaning company that creates value for customers, supports its employees in work and life</p>
    <a class="more" href="#">LEARN MORE &nbsp;»</a>
  </article>
  <article class="value-card" style="left:790px">
    <div class="value-icon"><svg width="50" height="50" viewBox="0 0 50 50" fill="none" stroke="#fff" stroke-width="2.5"><rect x="8" y="10" width="34" height="24" rx="2"/><path d="M14 28l7-8 6 5 9-10M25 34v8M18 42h14"/></svg></div>
    <h3>OUR STRATEGY</h3>
    <p>To differentiate ourselves through a prevailing focus on customer service, in everything we do and every interaction we have.</p>
    <a class="more" href="#">LEARN MORE &nbsp;»</a>
  </article>
</section>

<section class="services">
  <p class="eyebrow">What We Do</p>
  <h2 class="section-title">OUR SERVICES</h2>

  <article class="service-card" style="left:111px;top:182px">
    <div class="service-photo" role="img" aria-label="Stainless steel commercial kitchen equipment" style="background:linear-gradient(90deg,#163a78 0%,rgba(22,58,120,.85) 45%,#8fa3b8 70%,#c9d3dc 100%)"></div>
    <div class="service-text"><h3>Equipment Cleaning and Sanitisation Services</h3><p>Lorem ipsum dolor sit amet, consectetur adipiscing elit, sed do eiusmod incididunt ut labore et dolore magna</p><a class="more" href="#">LEARN MORE ➜</a></div>
  </article>
  <article class="service-card" style="left:615px;top:182px">
    <div class="service-photo" role="img" aria-label="Pressure washer cleaning paving beside a lawn" style="background:linear-gradient(90deg,#163a78 0%,rgba(22,58,120,.85) 45%,#7f8c6a 70%,#3f4a3a 100%)"></div>
    <div class="service-text"><h3>High pressure gurney &amp; play ground equipment cleaning</h3><p>Lorem ipsum dolor sit amet, consectetur adipiscing elit, sed do eiusmod incididunt ut</p><a class="more" href="#">LEARN MORE ➜</a></div>
  </article>
  <article class="service-card" style="left:111px;top:472px">
    <div class="service-photo" role="img" aria-label="Glass office tower with a window cleaning lift" style="background:linear-gradient(90deg,#163a78 0%,rgba(22,58,120,.85) 45%,#2f6fb0 70%,#123a70 100%)"></div>
    <div class="service-text"><h3>General Cleaning &amp; Property Facilities Management</h3><p>Lorem ipsum dolor sit amet, consectetur adipiscing elit, sed do eiusmod incididunt ut</p><a class="more" href="#">LEARN MORE ➜</a></div>
  </article>
  <article class="service-card" style="left:615px;top:472px">
    <div class="service-photo" role="img" aria-label="Recruiter reviewing a resume at a desk" style="background:linear-gradient(90deg,#163a78 0%,rgba(22,58,120,.85) 45%,#8d939c 70%,#e9ebee 100%)"></div>
    <div class="service-text"><h3>Project and Recruiting Services</h3><p>Lorem ipsum dolor sit amet, consectetur adipiscing elit, sed do eiusmod incididunt ut labore et dolore magna</p><a class="more" href="#">LEARN MORE ➜</a></div>
  </article>

  <a class="btn" href="#">LEARN MORE ABOUT SERVICES</a>
</section>

<section class="company">
  <div class="company-photo" role="img" aria-label="Collage of cleaning and facility photographs"></div>
  <h2>COMPANY <span class="accent">INFORMATION</span></h2>
  <p>Lorem ipsum dolor sit amet, consectetur adipiscing elit, sed eiusmod tempor incididunt ut labore et dolore magna aliqua. Ut enim ad minim veniam, quis nostrud exercitation ullamco laboris nisi ut aliquip ex ea commodo consequat. Duis aute irure dolor in reprehenderit in voluptate velit esse cillum dolore eu fugiat nulla pariatur. Excepteur sint occaecat cupidatat non proident, sunt in culpa qui officia deserunt mollit anim id est laborum.</p>
  <a class="btn" href="#">READ MORE <span class="dot"></span></a>
</section>

<section class="portfolio">
  <svg class="abs" style="left:0;top:0" width="1200" height="80" viewBox="0 0 1200 80">
    <path d="M0 0 H1200 V8 Q600 70 0 8Z" fill="#fff"/>
    <path d="M90 22 Q600 96 1110 22 Q600 70 90 22Z" fill="#fb3c07"/>
  </svg>
  <h2 class="section-title">OUR <span class="accent">PORTFOLIO</span></h2>
  <div class="tile" role="img" aria-label="Worker pressure washing a timber deck" style="left:113px;top:208px;width:490px;height:246px;background:linear-gradient(120deg,#6f6558,#a08a6c 55%,#6f8a3e)"></div>
  <div class="tile" role="img" aria-label="Clean stainless commercial kitchen" style="left:615px;top:208px;width:232px;height:246px;background:linear-gradient(180deg,#d8dadc,#9aa0a6)"></div>
  <div class="tile" role="img" aria-label="Fryer baskets in a commercial kitchen" style="left:855px;top:208px;width:232px;height:246px;background:linear-gradient(180deg,#5a4a40,#b9bcc0)"></div>
  <div class="tile" role="img" aria-label="Children's playground equipment" style="left:113px;top:466px;width:242px;height:244px;background:linear-gradient(180deg,#bfd1e3,#b36a3c 70%,#8d8770)"></div>
  <div class="tile" role="img" aria-label="Gloved hands cleaning conveyor rollers" style="left:363px;top:466px;width:240px;height:244px;background:linear-gradient(135deg,#3e5658,#a9b0a4 50%,#546a66)"></div>
  <div class="tile" role="img" aria-label="Technician in protective clothing at industrial machinery" style="left:615px;top:466px;width:472px;height:244px;background:linear-gradient(90deg,#9aa3a0,#cfd6d8 50%,#7fb2cf)"></div>
  <a class="btn" href="#">VIEW MORE <span class="dot"></span></a>
  <svg class="abs" style="left:0;top:856px" width="1200" height="80" viewBox="0 0 1200 80">
    <path d="M90 62 Q600 -6 1110 62 Q600 18 90 62Z" fill="#fb3c07"/>
    <path d="M0 80 V70 Q600 0 1200 70 V80Z" fill="#fff"/>
  </svg>
</section>

<section class="contact">
  <div class="touch-box">
    <h2>GET IN TOUCH</h2>
    <div class="touch-item"><span class="ico"><svg width="14" height="18" viewBox="0 0 14 18"><path d="M7 0a7 7 0 00-7 7c0 5 7 11 7 11s7-6 7-11a7 7 0 00-7-7zm0 9.5A2.5 2.5 0 117 4.5a2.5 2.5 0 010 5z" fill="#12377a"/></svg></span><h3>LET ME OUT</h3><p>378 SW Lorem ipsum dolor sit<br>amet, consectetur</p></div>
    <div class="touch-item"><span class="ico"><svg width="16" height="16" viewBox="0 0 24 24"><path fill="#12377a" d="M6.6 10.8a15.2 15.2 0 006.6 6.6l2.2-2.2a1 1 0 011-.25 11.4 11.4 0 003.6.6 1 1 0 011 1V20a1 1 0 01-1 1A17 17 0 013 4a1 1 0 011-1h3.5a1 1 0 011 1c0 1.25.2 2.45.6 3.6a1 1 0 01-.25 1z"/></svg></span><h3>PHONE</h3><p>(07) 5510 2047</p></div>
    <div class="touch-item"><span class="ico"><svg width="16" height="12" viewBox="0 0 16 12"><rect width="16" height="12" rx="1.5" fill="#12377a"/><path d="M1 1l7 5 7-5" stroke="#fff" stroke-width="1.4" fill="none"/></svg></span><h3>EMAIL</h3><p>info@brightvale.com</p></div>
    <div class="touch-item"><span class="ico"><svg width="16" height="16" viewBox="0 0 16 16"><rect x="4" y="0" width="8" height="5" fill="#12377a"/><rect x="0" y="5" width="16" height="8" rx="1.5" fill="#12377a"/><rect x="4" y="10" width="8" height="6" fill="#12377a" stroke="#fff"/></svg></span><h3>FAX</h3><p>123 456 7890</p></div>
  </div>

  <form class="contact-form">
    <h2>CONTACT US</h2>
    <div class="field" style="left:0;top:62px;width:222px">⚲ Name</div>
    <div class="field" style="left:235px;top:62px;width:210px">✆ Phone Number</div>
    <div class="field" style="left:0;top:135px;width:222px">✉ Email Address</div>
    <div class="field" style="left:235px;top:135px;width:210px">✎ Subject</div>
    <div class="field" style="left:0;top:208px;width:445px;height:48px;align-items:flex-start;padding-top:6px">☰ Message</div>
    <a class="btn" href="#">SUBMIT</a>
  </form>
</section>

<footer class="site-footer">
  <svg class="abs" style="left:0;top:0" width="1200" height="110" viewBox="0 0 1200 110">
    <path d="M0 0 H1200 Q600 110 0 0Z" fill="#fff"/>
    <path d="M90 15 Q600 110 1110 15 Q600 80 90 15Z" fill="#fb3c07"/>
    <circle cx="600" cy="63" r="29" fill="#fff"/>
    <circle cx="600" cy="63" r="14" fill="#12377a"/>
  </svg>
  <div class="footer-col" style="left:113px"><h4>QUICK LINKS</h4><ul><li>Home</li><li>About</li><li>Services</li><li>Reviews</li><li>Gallery</li></ul></div>
  <div class="footer-col" style="left:349px"><h4>INFORMATION</h4><ul><li>Terms &amp; Conditions</li><li>Privacy Policy</li><li>Disclaimer</li><li>Site Map</li><li>Contact Us</li></ul></div>
  <div class="footer-col" style="left:615px"><h4>CONTACT INFO</h4>
    <div class="info-row"><span>☎</span>(07) 5510 2047</div>
    <div class="info-row"><span>⎙</span>(555) 014-277</div>
    <div class="info-row"><span>✉</span><u>info@brightvale.com</u></div>
    <div class="info-row"><span>⚲</span>378 SW Lorem ipsum dolor<br>sit amet, consectetur</div>
  </div>
  <div class="footer-col" style="left:952px"><h4>FOLLOW US</h4>
    <div class="social"><span></span>Socialpage</div>
    <div class="social"><span></span>Chirper</div>
    <div class="social"><span></span>Circles</div>
    <div class="social"><span></span>Worknet</div>
  </div>
  <p class="copyright">Copyrights © Brightvale 2020 | Allrights Reserved</p>
</footer>

</body>
</html>
```